Business Card for Multi-Brand Sportswear Company

We are looking for a business card which represents our company and the multiple brands within it.

The company: Fen Athletics (LTD)
The brands: Fen, TavaPuni, ElmStretch, Grit and Rain

Employees using these cards would be representing Fen Athletics, rather than any of the individual brands. You will see a current design within the uploaded files, to give some inspiration. The actual text of the brands is not necessary, but the logos should be on there is some format.

Our creative minds on this are stretched, so we are looking for someone to make this their own, and show us what a good business card should look like.

We may like to get these printed with spot gloss, so keep that in mind with your designs.

www.fenathletics.co.uk

Industry/Entity Type

Business

Contact Information for Business Card

Leo Pemberton-Hale
Operations Manager
(+44) 1632 960 418
Leo@fenathletics.co.uk
www.fenathletics.co.uk

Font styles to use
Sans Serif
Other font styles liked:
• Eurostile

Colors
ffffff

Requirements
Nice to have
• Dark (black) background

```html
<!DOCTYPE html>
<html lang="en">
<head>
<meta charset="utf-8">
<title>Fen Athletics – Business Card</title>
<link rel="stylesheet" href="https://fonts.googleapis.com/css2?family=Exo+2:wght@400;500;700&display=swap">
<style>
  :root {
    --stage: #ececec;
    --card: #2a2a2b;
    --card-deep: #1f1f20;
    --facet: #333334;
    --red: #c8202a;
    --white: #ffffff;
    --soft: #e4e4e4;
    --brand-muted: #8a8a8a;
  }
  * { margin: 0; padding: 0; box-sizing: border-box; }
  html, body { width: 1200px; height: 586px; overflow: hidden; }
  body {
    background: var(--stage);
    font-family: "Exo 2", sans-serif;
    color: var(--white);
    position: relative;
  }
  .card {
    position: absolute;
    top: 129px;
    width: 502px;
    height: 300px;
    overflow: hidden;
  }
  .card--front { left: 65px; }
  .card--back { left: 608px; }
  .card__texture {
    position: absolute; inset: 0;
    background: linear-gradient(135deg, var(--facet) 0%, var(--card) 40%, var(--card-deep) 70%, var(--card) 100%);
  }
  .tab {
    position: absolute;
    top: 58px;
    width: 15px;
    height: 186px;
    background: var(--red);
  }
  .tab--left { left: 0; border-radius: 0 12px 12px 0; }
  .tab--right { right: 0; border-radius: 12px 0 0 12px; }

  .wordmark {
    position: absolute;
    font-weight: 700;
    color: var(--white);
    text-transform: uppercase;
    white-space: nowrap;
    display: flex;
    align-items: center;
  }
  .wordmark__dot {
    display: inline-block;
    background: var(--red);
    border-radius: 50%;
  }
  .card--front .wordmark {
    left: 0; right: 0; top: 120px;
    justify-content: center;
    font-size: 44px;
    letter-spacing: 2px;
    gap: 14px;
  }
  .card--front .wordmark__dot { width: 18px; height: 18px; }
  .card--back .wordmark {
    left: 0; right: 0; top: 30px;
    justify-content: center;
    font-size: 28px;
    letter-spacing: 1.5px;
    gap: 10px;
  }
  .card--back .wordmark__dot { width: 12px; height: 12px; }

  .holder {
    position: absolute;
    right: 286px;
    top: 164px;
    text-align: right;
    white-space: nowrap;
  }
  .holder__name { font-size: 16px; font-weight: 700; letter-spacing: .3px; }
  .holder__role { font-size: 12px; font-weight: 400; color: var(--soft); margin-top: 3px; }

  .divider {
    position: absolute;
    left: 234px; top: 127px;
    width: 2px; height: 112px;
    background: linear-gradient(to bottom, transparent, var(--red) 50%, transparent);
  }

  .contact {
    position: absolute;
    left: 264px; top: 118px;
    list-style: none;
  }
  .contact__item {
    display: flex; align-items: center; gap: 7px;
    font-size: 11.5px; color: var(--soft);
    height: 22px;
    white-space: nowrap;
  }
  .contact__icon { width: 12px; height: 12px; fill: var(--red); flex: none; }
  .address {
    position: absolute;
    left: 264px; top: 210px;
    font-size: 12px; font-weight: 700; line-height: 16px;
    font-style: normal;
  }

  .brands {
    position: absolute;
    left: 0; right: 0; top: 274px;
    display: flex; justify-content: center; align-items: center; gap: 12px;
    font-size: 10px; font-weight: 500; color: var(--brand-muted);
    list-style: none;
  }
  .brands__item--lead { color: var(--white); }
</style>
</head>
<body>

<section class="card card--front" aria-label="Card front">
  <div class="card__texture" role="img" aria-label="Dark faceted low-poly background texture"></div>
  <span class="tab tab--left"></span>
  <span class="tab tab--right"></span>
  <div class="wordmark"><span class="wordmark__dot"></span>Fen Athletics</div>
</section>

<section class="card card--back" aria-label="Card back">
  <div class="card__texture" role="img" aria-label="Dark faceted low-poly background texture"></div>
  <span class="tab tab--left"></span>
  <span class="tab tab--right"></span>
  <div class="wordmark"><span class="wordmark__dot"></span>Fen Athletics</div>

  <div class="holder">
    <p class="holder__name">Leo Pemberton-Hale</p>
    <p class="holder__role">Operations Manager</p>
  </div>

  <span class="divider"></span>

  <ul class="contact">
    <li class="contact__item">
      <svg class="contact__icon" viewBox="0 0 16 16"><path d="M3 2h3l1.5 3.5-2 1.3a8 8 0 0 0 3.7 3.7l1.3-2L14 10v3a1 1 0 0 1-1 1A11 11 0 0 1 2 3a1 1 0 0 1 1-1z"/></svg>
      (+44) 1632 960 418
    </li>
    <li class="contact__item">
      <svg class="contact__icon" viewBox="0 0 16 16"><path d="M4 1h8v4H4zM1 6h14v6h-3v3H4v-3H1zM5 10v4h6v-4z"/></svg>
      (555) 014-2273
    </li>
    <li class="contact__item">
      <svg class="contact__icon" viewBox="0 0 16 16"><path d="M1 3h14v10H1zM2 4l6 5 6-5v1L8 10 2 5z" fill-rule="evenodd"/></svg>
      Leo@fenathletics.co.uk
    </li>
    <li class="contact__item">
      <svg class="contact__icon" viewBox="0 0 16 16"><path d="M8 1a7 7 0 1 0 0 14A7 7 0 0 0 8 1zm0 1.5c.8 0 1.8 1.6 2.1 4.5H5.9C6.2 4.1 7.2 2.5 8 2.5zM2.6 7h1.8c.1-1.6.5-3 1-3.9A5.5 5.5 0 0 0 2.6 7zm8.9 0h1.9a5.5 5.5 0 0 0-2.9-3.9c.5.9.9 2.3 1 3.9zM2.6 9a5.5 5.5 0 0 0 2.8 3.9c-.5-.9-.9-2.3-1-3.9zm3.3 0c.3 2.9 1.3 4.5 2.1 4.5s1.8-1.6 2.1-4.5zm5.6 0c-.1 1.6-.5 3-1 3.9A5.5 5.5 0 0 0 13.4 9z"/></svg>
      www.fenathletics.co.uk
    </li>
  </ul>

  <address class="address">Kestrel Yard, Aldwick<br>Harlow, HX9 4PL</address>

  <ul class="brands" aria-label="Group brands">
    <li class="brands__item">ElmStretch</li>
    <li class="brands__item">Grit and Rain</li>
    <li class="brands__item">TavaPuni</li>
    <li class="brands__item brands__item--lead">Fen</li>
  </ul>
</section>

</body>
</html>
```